Varnex Consulting Business card design.

See our website www.varnexconsulting.example which will give you a good idea of what we are about. The font is called 'Play'.

I'd like a standout business card in keeping with the themes and branding on the website

Target Market(s)

professionals. HR directors

Industry/Entity Type

Business

Contact Information for Business Card

Varnex Consulting PO Box 3172 Merrowdale NSW 2291 1300 485 193 Gavin Threlkeld Principal email: career@varnexconsulting.example ABN: 71203948865

Font styles to use
Other font styles liked:
• Play

Requirements
Must have
• Must have same design colours and branding as website.
• On back I'd prefer a list of the things we do which appears below the name at the header on the website

```html
<!DOCTYPE html>
<html lang="en">
<head>
<meta charset="utf-8">
<title>Varnex Consulting – Business Card</title>
<link href="https://fonts.googleapis.com/css2?family=Play:wght@400;700&display=swap" rel="stylesheet">
<style>
  :root {
    --navy: #0a1d2c;
    --blue: #2f87c2;
    --brand-blue: #2b8fd6;
    --white: #ffffff;
    --wave-white: #eceef0;
    --ink: #0b1520;
    --page: #e4e6e9;
  }
  * { box-sizing: border-box; margin: 0; padding: 0; }
  html, body {
    width: 1200px; height: 892px; overflow: hidden;
    background: var(--page);
    font-family: 'Play', sans-serif;
  }
  .sheet {
    width: 1200px; height: 892px;
    display: flex; flex-direction: column; align-items: center;
    justify-content: center; gap: 20px;
  }
  .card {
    position: relative;
    width: 680px; height: 416px;
    background: var(--navy);
    overflow: hidden;
    box-shadow: 0 4px 14px rgba(0,0,0,.18);
  }
  .card__wave { position: absolute; inset: 0; width: 100%; height: 100%; }

  .brand {
    font-size: 44px; letter-spacing: 1px; line-height: 1; white-space: nowrap;
  }
  .brand__first { color: var(--white); }
  .brand__second { color: var(--brand-blue); }
  .services {
    color: var(--brand-blue); font-size: 15px; letter-spacing: 1.6px; white-space: nowrap;
  }
  .services .sep { color: var(--white); margin: 0 6px; }

  /* Front */
  .front .brand { position: absolute; left: 36px; top: 50px; font-size: 40px; }
  .front .services { position: absolute; left: 38px; top: 104px; font-size: 13px; letter-spacing: 1.4px; }
  .front .services .sep { margin: 0 5px; }
  .contact {
    position: absolute; right: 36px; top: 196px;
    text-align: right; color: var(--ink);
  }
  .contact__name { font-size: 22px; font-weight: 700; line-height: 1.1; }
  .contact__role { font-size: 16px; margin-bottom: 14px; }
  .contact__line {
    font-size: 14px; line-height: 1.5;
    display: flex; justify-content: flex-end; align-items: center; gap: 8px;
  }
  .contact__line--gap { margin-top: 14px; }
  .icon {
    width: 14px; height: 14px; background: var(--white); border-radius: 2px;
    display: inline-flex; align-items: center; justify-content: center;
  }
  .icon svg { width: 10px; height: 10px; }

  /* Back */
  .back .brand { position: absolute; left: 0; right: 0; top: 50px; text-align: center; }
  .back .services { position: absolute; left: 0; right: 0; top: 108px; text-align: center; }
  .gallery {
    position: absolute; left: 30px; right: 30px; bottom: 34px;
    display: flex; justify-content: space-between;
  }
  .gallery__photo { width: 196px; height: 196px; }
  .gallery__photo--surf { background: linear-gradient(160deg, #d9dde0, #8d969c 60%, #eef1f2); }
  .gallery__photo--track { background: linear-gradient(180deg, #c9b0a4, #a9887c 55%, #7b4d45); }
  .gallery__photo--snow { background: linear-gradient(180deg, #1c5fb8, #4d90dc 55%, #f2f6fa 80%, #dce6f0); }
</style>
</head>
<body>
<main class="sheet">

  <section class="card front" aria-label="Business card front">
    <svg class="card__wave" viewBox="0 0 680 416" preserveAspectRatio="none" aria-hidden="true">
      <path fill="var(--wave-white)" d="M0,312 C220,300 360,270 430,190 C490,120 560,30 680,8 L680,416 L0,416 Z"/>
      <path fill="var(--blue)" d="M0,352 C230,345 390,310 460,225 C520,150 590,65 680,48 L680,416 L0,416 Z"/>
    </svg>

    <div class="brand"><span class="brand__first">VARNEX</span> <span class="brand__second">CONSULTING</span></div>
    <div class="services">Search &amp; Select<span class="sep">|</span>Career<span class="sep">|</span>Coaching<span class="sep">|</span>Leadership<span class="sep">|</span>Outplacement</div>

    <div class="contact">
      <div class="contact__name">Gavin Threlkeld</div>
      <div class="contact__role">Principal</div>
      <div class="contact__line">ABN: 71203948865
        <span class="icon"><svg viewBox="0 0 10 10"><rect x="1.5" y="2" width="7" height="6" fill="none" stroke="var(--blue)" stroke-width="1.2"/></svg></span>
      </div>
      <div class="contact__line">1300 485 193
        <span class="icon"><svg viewBox="0 0 10 10"><path d="M2,1 L4,1 L4.6,3 L3.4,4 C4,5.4 4.8,6.2 6,6.8 L7,5.6 L9,6.2 L9,8.2 C5,8.6 1.4,5 2,1 Z" fill="var(--blue)"/></svg></span>
      </div>
      <div class="contact__line contact__line--gap">career@varnexconsulting.example
        <span class="icon"><svg viewBox="0 0 10 10"><rect x="1" y="2.5" width="8" height="5.5" fill="none" stroke="var(--blue)" stroke-width="1.1"/><path d="M1,2.5 L5,5.5 L9,2.5" fill="none" stroke="var(--blue)" stroke-width="1.1"/></svg></span>
      </div>
      <div class="contact__line">PO Box 3172 Merrowdale NSW 2291
        <span class="icon"><svg viewBox="0 0 10 10"><path d="M5,9 C3,6.5 2,5 2,3.6 A3,3 0 0 1 8,3.6 C8,5 7,6.5 5,9 Z" fill="var(--blue)"/></svg></span>
      </div>
    </div>
  </section>

  <section class="card back" aria-label="Business card back">
    <div class="brand"><span class="brand__first">VARNEX</span> <span class="brand__second">CONSULTING</span></div>
    <div class="services">Search &amp; Select<span class="sep">|</span>Career<span class="sep">|</span>Coaching<span class="sep">|</span>Leadership<span class="sep">|</span>Outplacement</div>
    <div class="gallery">
      <div class="gallery__photo gallery__photo--surf" role="img" aria-label="Photo of a surfer riding through white water"></div>
      <div class="gallery__photo gallery__photo--track" role="img" aria-label="Photo of a sprinter's hands on the start line of a running track"></div>
      <div class="gallery__photo gallery__photo--snow" role="img" aria-label="Photo of a snowboarder jumping against a blue sky above a snowy peak"></div>
    </div>
  </section>

</main>
</body>
</html>
```